TALMORK

The business want a professional looking business card. We have a scetch we will add but want the extra upgrade, and would like more suggestions for variations of our business cards.

```html
<!DOCTYPE html>
<html lang="en">
<head>
<meta charset="utf-8">
<title>TALMORK – Business Card</title>
<link rel="stylesheet" href="https://fonts.googleapis.com/css2?family=Playfair+Display:wght@400;500&family=Open+Sans:wght@400&display=swap">
<style>
  :root {
    --backdrop: #e6ddb9;
    --paper: #ffffff;
    --slate: #4a5764;
    --slate-dark: #3d4854;
    --ink: #4f5a66;
    --gold: #c9a35f;
    --gold-soft: #d8b878;
  }
  * { box-sizing: border-box; margin: 0; padding: 0; }
  html, body {
    width: 1200px; height: 926px; overflow: hidden;
    background: var(--backdrop);
  }
  .sheet {
    position: relative; width: 1200px; height: 926px;
    display: flex; align-items: center; justify-content: center; gap: 40px;
  }
  .card {
    position: relative; width: 520px; height: 297px;
    box-shadow: 0 10px 28px rgba(90, 70, 20, 0.22);
    overflow: hidden;
  }
  /* Front */
  .card--front { background: var(--paper); }
  .card__band {
    position: absolute; left: 0; right: 0; bottom: 0; height: 24px;
    background: var(--slate);
    border-top: 2px solid var(--gold);
  }
  .contact-block { position: absolute; left: 40px; top: 38px; }
  .person__name {
    font-family: "Playfair Display", serif; font-weight: 400;
    font-size: 25px; color: var(--gold); letter-spacing: 0.5px;
  }
  .person__role {
    font-family: "Open Sans", sans-serif; font-size: 12.5px;
    color: var(--ink); margin-top: 2px;
  }
  .contact-list { list-style: none; margin-top: 22px; }
  .contact-list__item {
    display: flex; align-items: center; gap: 10px;
    font-family: "Open Sans", sans-serif; font-size: 12px;
    color: var(--ink); height: 22px;
  }
  .contact-list__icon { width: 14px; height: 14px; flex: none; }
  .front-brand {
    position: absolute; right: 40px; top: 150px;
    font-family: "Playfair Display", serif; font-weight: 500;
    font-size: 26px; letter-spacing: 7px; color: var(--slate);
  }
  /* Back */
  .card--back {
    background: linear-gradient(160deg, var(--slate) 0%, var(--slate-dark) 100%);
    display: flex; align-items: center; justify-content: center;
  }
  .back-brand {
    font-family: "Playfair Display", serif; font-weight: 500;
    font-size: 34px; letter-spacing: 9px; color: var(--gold-soft);
  }
</style>
</head>
<body>
<main class="sheet">
  <section class="card card--front" aria-label="Business card front">
    <div class="contact-block">
      <h1 class="person__name">Aksel Brandvik</h1>
      <p class="person__role">Director of Marketing</p>
      <ul class="contact-list">
        <li class="contact-list__item">
          <svg class="contact-list__icon" viewBox="0 0 14 14" fill="none" stroke="var(--gold)" stroke-width="1">
            <rect x="3.5" y="0.5" width="7" height="13" rx="1.2"/><line x1="6" y1="11.5" x2="8" y2="11.5"/>
          </svg>004 712 340 556</li>
        <li class="contact-list__item">
          <svg class="contact-list__icon" viewBox="0 0 14 14" fill="none" stroke="var(--gold)" stroke-width="1">
            <rect x="0.5" y="2.5" width="13" height="9"/><polyline points="0.5,2.5 7,8 13.5,2.5"/>
          </svg>hello@talmork.llc</li>
        <li class="contact-list__item">
          <svg class="contact-list__icon" viewBox="0 0 14 14" fill="none" stroke="var(--gold)" stroke-width="1">
            <circle cx="7" cy="7" r="6.3"/><ellipse cx="7" cy="7" rx="2.8" ry="6.3"/><line x1="0.7" y1="7" x2="13.3" y2="7"/><line x1="1.6" y1="3.8" x2="12.4" y2="3.8"/><line x1="1.6" y1="10.2" x2="12.4" y2="10.2"/>
          </svg>www.talmork.llc</li>
      </ul>
    </div>
    <p class="front-brand">TALMORK</p>
    <div class="card__band"></div>
  </section>

  <section class="card card--back" aria-label="Business card back">
    <p class="back-brand">TALMORK</p>
  </section>
</main>
</body>
</html>
```